Landingpage Design X-Mas Invitation

Every year we invite customers to a special X-Mas Apéro. Since we are an IT-Company we handle the registration process by a landingpage. For this we need a design for the event 2016. The content will be the same as 2015 (you will finde the design attached from last year. There will be an additional job for creating the E-Mail.

Target Market(s)

Customers of IT Company, medium Companys in Central Switzerland

Industry/Entity Type

It Company

Number of Pages Required

1 page

Requirements
Must have
• Christmas Style

```html
<!DOCTYPE html>
<html lang="de">
<head>
<meta charset="utf-8">
<title>Lumara IT Solutions – Weihnachts-Apéro 2016</title>
<link href="https://fonts.googleapis.com/css2?family=Open+Sans:wght@400;600;700&family=Raleway:wght@500&display=swap" rel="stylesheet">
<style>
  :root {
    --brand-red: #c0412b;
    --text-grey: #6b6b6b;
    --hero-bg: #f6f6f6;
    --band-bg: #ffffff;
    --form-red-light: #d65a40;
    --form-red-dark: #b7311f;
    --button-red: #a52d1c;
    --input-top: #ffffff;
    --input-bottom: #e9e9e9;
    --input-text: #555555;
    --footer-bg: #343434;
    --footer-text: #dddddd;
    --partner-shape: #d4d4d4;
  }
  * { box-sizing: border-box; margin: 0; padding: 0; }
  html, body { width: 1200px; height: 1089px; overflow: hidden; }
  body { font-family: "Open Sans", sans-serif; position: relative; background: var(--band-bg); }

  .hero {
    position: absolute; left: 0; top: 0; width: 1200px; height: 536px;
    background: radial-gradient(ellipse at 45% 30%, #ffffff 0%, var(--hero-bg) 60%, #ececec 100%);
  }
  .brand {
    position: absolute; left: 124px; top: 62px;
    display: flex; align-items: center; gap: 10px;
    color: var(--brand-red); font-weight: 700; font-size: 40px; letter-spacing: -0.5px;
  }
  .brand-mark { width: 16px; height: 16px; background: var(--brand-red); }
  .headline {
    position: absolute; left: 125px; top: 213px; width: 490px;
    font-family: "Raleway", sans-serif; font-weight: 500;
    font-size: 28px; line-height: 33px; color: var(--brand-red);
  }
  .intro {
    position: absolute; left: 125px; top: 368px; width: 400px;
    font-size: 15.5px; line-height: 24px; color: var(--text-grey);
  }
  .tree {
    position: absolute; left: 675px; top: 0; width: 320px; height: 536px;
    background: radial-gradient(ellipse 45% 55% at 50% 58%, #2f6b2a 0%, #3f7d34 45%, rgba(246,246,246,0) 100%);
  }

  .partners {
    position: absolute; left: 0; top: 536px; width: 1200px; height: 87px;
    display: flex; align-items: center; justify-content: center; gap: 22px;
    background: var(--band-bg);
  }
  .partner { background: var(--partner-shape); height: 20px; border-radius: 3px; }
  .partner.round { width: 34px; height: 34px; border-radius: 50%; }

  .registration {
    position: absolute; left: 0; top: 623px; width: 1200px; height: 404px;
    background: linear-gradient(160deg, var(--form-red-light) 0%, #c9462e 50%, var(--form-red-dark) 100%);
  }
  .column { position: absolute; top: 62px; width: 429px; }
  .column.guest { left: 162px; }
  .column.companion { left: 616px; }
  .column h2 {
    font-weight: 400; font-size: 23px; color: #ffffff; margin-bottom: 14px; height: 28px;
  }
  .field {
    display: block; width: 429px; height: 42px; margin-bottom: 11px;
    background: linear-gradient(var(--input-top), var(--input-bottom));
    border: 1px solid #cfcfcf; padding: 0 20px 0 20px;
    font-family: inherit; font-size: 14px; color: var(--input-text);
  }
  .companion .field { padding-left: 15px; }
  .field::placeholder { color: var(--input-text); }
  .more-link {
    display: block; margin-top: 13px; font-size: 16px; color: #ffffff; text-decoration: none;
  }
  .submit {
    margin-top: 9px; margin-left: 3px; width: 142px; height: 40px;
    background: var(--button-red); border: 2px solid #ffffff; color: #ffffff;
    font-family: inherit; font-size: 19px;
  }

  .footer {
    position: absolute; left: 0; top: 1027px; width: 1200px; height: 62px;
    background: var(--footer-bg); color: var(--footer-text);
    font-size: 13px; text-align: center; line-height: 62px;
  }
  .footer span { margin: 0 2px; }
</style>
</head>
<body>
  <header class="hero">
    <div class="brand"><span>Lumara IT Solutions</span><span class="brand-mark"></span></div>
    <h1 class="headline">Ob Sie den ganzen Abend bleiben oder nur kurz nach dem Weihnachts-Shopping vorbeischauen, ist ganz Ihnen überlassen.</h1>
    <p class="intro">Wir freuen uns sehr, wenn Sie uns die Gelegenheit geben, Ihnen mit dieser Einladung für die erfolgreiche Zusammenarbeit herzlichst zu danken.</p>
    <div class="tree" role="img" aria-label="Geschmückter Weihnachtsbaum mit roten und goldenen Kugeln und Stern"></div>
  </header>

  <section class="partners" aria-label="Partner">
    <div class="partner round"></div>
    <div class="partner" style="width:110px"></div>
    <div class="partner" style="width:56px"></div>
    <div class="partner" style="width:42px"></div>
    <div class="partner" style="width:110px"></div>
    <div class="partner" style="width:72px"></div>
    <div class="partner" style="width:60px"></div>
    <div class="partner" style="width:82px"></div>
    <div class="partner" style="width:52px"></div>
    <div class="partner" style="width:80px"></div>
    <div class="partner" style="width:108px"></div>
  </section>

  <section class="registration" role="img" aria-label="Rot getöntes Foto einer Tastatur im Hintergrund">
    <form class="column guest">
      <h2>Ihre Anmeldung</h2>
      <input class="field" type="email" placeholder="Ihre E-Mail-Adresse">
      <input class="field" type="text" placeholder="Vorname">
      <input class="field" type="text" placeholder="Nachname">
      <a class="more-link" href="#">Weitere Begleitperson</a>
      <button class="submit" type="submit">Absenden</button>
    </form>
    <div class="column companion">
      <h2>Ihre Begleitperson</h2>
      <input class="field" type="text" placeholder="Vorname">
      <input class="field" type="text" placeholder="Nachname">
      <input class="field" type="text" placeholder="Firma (Optional)">
    </div>
  </section>

  <footer class="footer">
    <span>© 2016 Company Name</span> <span>All right reserved</span> <span>Term of Use</span>
  </footer>
</body>
</html>
```